Business Cards - Brightpath Horizon

need to design unique business card for my mortgage business. I need to design credit card style business card for my business or any unique idea that you might have

Target Market(s)

Home Loan customers

Industry/Entity Type

Mortgage Brokerage

Contact Information for Business Card

please design credit card style or very unique style business card

Colors

Designer to choose colors to be used in the design.

Requirements
Must have
• Name
• position
• Phone number
• fax number
• email address
• website address
• social media address
• All above fields will be provided once design in finalised

```html
<!DOCTYPE html>
<html lang="en">
<head>
<meta charset="utf-8">
<title>Brightpath Horizon – Business Card</title>
<link href="https://fonts.googleapis.com/css2?family=Work+Sans:wght@400;500&display=swap" rel="stylesheet">
<style>
  :root {
    --bg: #eceae6;
    --card-white: #ffffff;
    --brand-blue: #2f4a9e;
    --sky-blue: #1ba1e2;
    --accent-orange: #f28c1e;
    --ink: #474747;
    --white: #ffffff;
  }
  * { margin: 0; padding: 0; box-sizing: border-box; }
  html, body { width: 1200px; height: 1000px; overflow: hidden; }
  body {
    background: var(--bg);
    font-family: "Work Sans", Arial, sans-serif;
    position: relative;
  }
  .card {
    position: absolute;
    left: 255px;
    width: 666px;
    height: 380px;
    border-radius: 22px;
    overflow: hidden;
    box-shadow: 0 4px 10px rgba(0,0,0,0.18);
  }
  .card--front { top: 100px; background: var(--card-white); }
  .card--back { top: 520px; background: var(--brand-blue); }

  .brand-name {
    position: absolute;
    font-weight: 500;
    letter-spacing: 1px;
    text-align: center;
    line-height: 1.1;
  }
  .card--front .brand-name {
    left: 70px; top: 150px; width: 250px;
    font-size: 30px; color: var(--brand-blue);
  }
  .card--back .brand-name {
    left: 183px; top: 150px; width: 300px;
    font-size: 36px; color: var(--white);
  }

  .divider {
    position: absolute;
    left: 342px; top: 100px;
    width: 2px; height: 180px;
    background: var(--brand-blue);
  }
  .contact { position: absolute; left: 379px; top: 95px; color: var(--ink); }
  .contact__name {
    font-size: 25px; font-weight: 400; letter-spacing: 1.5px;
    color: var(--sky-blue); line-height: 1.1;
  }
  .contact__role { font-size: 15px; font-weight: 500; margin-top: 8px; }
  .contact__address { font-size: 15px; margin-top: 20px; line-height: 20px; }
  .contact__list { list-style: none; margin-top: 20px; font-size: 15px; line-height: 19px; }
  .contact__list li { display: flex; align-items: center; gap: 10px; }
  .contact__list svg { width: 10px; height: 10px; fill: var(--sky-blue); flex: none; }

  .bands { position: absolute; left: 0; bottom: 0; width: 666px; height: 32px; }
  .band--orange { fill: var(--accent-orange); }
  .band--blue { fill: var(--brand-blue); }

  .website {
    position: absolute; left: 0; right: 0; top: 334px;
    text-align: center; color: var(--white);
    font-size: 15px; letter-spacing: 1.5px;
  }
</style>
</head>
<body>
  <section class="card card--front" aria-label="Business card front">
    <div class="brand-name">Brightpath<br>Horizon</div>
    <div class="divider"></div>
    <div class="contact">
      <div class="contact__name">DANIEL CARTER</div>
      <div class="contact__role">Founder</div>
      <div class="contact__address">480 Harbor View Dr.<br>Coral Springs, FL 33071</div>
      <ul class="contact__list">
        <li><svg viewBox="0 0 10 10"><path d="M2 0.5 L3.6 2.6 L2.8 3.8 C3.4 5.2 4.6 6.5 6.1 7.2 L7.3 6.4 L9.5 8 L8.6 9.5 C4.5 9.4 0.7 5.5 0.5 1.4 Z"/></svg>555-214-7830</li>
        <li><svg viewBox="0 0 10 10"><path d="M0.5 2 H9.5 V8.5 H0.5 Z M1.4 2.8 V7.7 H8.6 V2.8 L5 5.4 Z" fill-rule="evenodd"/></svg>hello@brightpathhorizon.com</li>
        <li><svg viewBox="0 0 10 10"><circle cx="5" cy="5" r="4.5"/><path d="M0.5 5 H9.5 M5 0.5 C3 3 3 7 5 9.5 C7 7 7 3 5 0.5" stroke="#fff" stroke-width="0.7" fill="none"/></svg>www.BrightpathHorizon.com</li>
      </ul>
    </div>
    <svg class="bands" viewBox="0 0 666 32" preserveAspectRatio="none">
      <polygon class="band--orange" points="0,18 345,18 332,32 0,32"/>
      <polygon class="band--blue" points="370,2 666,2 666,32 340,32"/>
    </svg>
  </section>

  <section class="card card--back" aria-label="Business card back">
    <div class="brand-name">Brightpath<br>Horizon</div>
    <div class="website">www.yourwebsite.com</div>
  </section>
</body>
</html>
```